2026 Varlo Kestin LWB Vehicle Wrap Design for Tallwood Electrical and Refrigeration Work Vans

We are Tallwood Electrical and Refrigeration — a Perth-based commercial electrical, air conditioning and refrigeration company. We service commercial buildings, homes and luxury residential jobs across the metro area and remote WA.
We need a clean, professional and high-impact full vehicle wrap design for our work vans. The vans are our mobile billboards, so the design needs to look sharp from a distance, communicate trust and competence, and clearly show what we do.
Must include:

Our company name: Tallwood Electrical and Refrigeration
Tagline options (you can choose the strongest placement or suggest alternatives):
“Electrical | Air Conditioning | Refrigeration – Perth & Remote WA”
Licence numbers "AU531207 and EC42918"
Phone number: 0412 555 318
Website: tallwoodelectricalrefrigeration.com.au
Email: admin@tallwoodelectricalrefrigeration.com.au
Our existing logo (will be uploaded)

Style we want:

Professional, modern and trustworthy
Bold enough to stand out on the road but not flashy or overly busy
Clean hierarchy so the company name and phone number are readable at speed
Strong use of contrast

Colour preferences:

Prefer designs that work with our existing branding (we will upload the logo and brand colours)
Open to strong, professional colour combinations (navy/dark blue, black, white, and one accent colour such as orange, red or electric blue often work well in the trades)

Avoid:

Cluttered designs with too much text
Cartoonish or overly “tradie” looking graphics
Designs that look cheap or dated

Additional notes:

Design should scale well so we can use the same concept across multiple vans
We will need print-ready files (high-res, layered) at the end

Please upload your best concepts. We will give clear feedback and work with the winning designer to refine the final artwork for production.

Target Market(s)

commercial buildings, homes and luxury residential jobs across the metro area and remote WA.

Industry/Entity Type

Electrical, Air Conditioning and Refrigeration

Colors
0054AA
0677BA
7BADD7
CADEEF
E8F1F8

Requirements
Must have
• Our company name: Tallwood Electrical and Refrigeration Tagline options (you can choose the strongest placement or suggest alternatives): “Electrical | Air Conditioning | Refrigeration – Perth & Remote WA” Licence numbers "AU531207 and EC42918" Phone number: 0412 555 318 Website: tallwoodelectricalrefrigeration.com.au Email: admin@tallwoodelectricalrefrigeration.com.au Our existing logo (will be uploaded)
Nice to have
• Professional, modern and trustworthy Bold enough to stand out on the road but not flashy or overly busy Clean hierarchy so the company name and phone number are readable at speed Strong use of contrast
Should not have
• Cluttered designs with too much text Cartoonish or overly “tradie” looking graphics Designs that look cheap or dated

```html
<!DOCTYPE html>
<html lang="en">
<head>
<meta charset="utf-8">
<title>Tallwood Electrical and Refrigeration – Van Wrap Side</title>
<link rel="stylesheet" href="https://fonts.googleapis.com/css2?family=Poppins:wght@400;600;700&display=swap">
<style>
  :root {
    --brand-blue: #0a68cc;
    --brand-blue-deep: #0054aa;
    --wrap-grey: #8a8b8d;
    --body-white: #f1f1ee;
    --canvas: #ffffff;
    --text-light: #ffffff;
    --text-dark: #3a3a3a;
  }
  html, body {
    margin: 0;
    padding: 0;
    width: 1200px;
    height: 513px;
    overflow: hidden;
    background: var(--canvas);
  }
  .wrap-side {
    position: relative;
    width: 1200px;
    height: 513px;
    font-family: "Poppins", sans-serif;
  }
  .wrap-shapes {
    position: absolute;
    inset: 0;
  }
  .services {
    position: absolute;
    left: 137px;
    top: 106px;
    width: 220px;
    text-align: center;
    color: var(--text-light);
    font-size: 11.5px;
    line-height: 16px;
    letter-spacing: 0.2px;
    margin: 0;
  }
  .services-rule {
    width: 28px;
    height: 1px;
    background: var(--text-light);
    margin: 8px auto 8px;
  }
  .service-area {
    font-weight: 600;
    font-size: 11.5px;
  }
  .phone {
    position: absolute;
    left: 114px;
    top: 254px;
    width: 250px;
    text-align: center;
    color: var(--text-light);
    font-weight: 700;
    font-size: 32px;
    line-height: 44px;
    letter-spacing: 0.2px;
    margin: 0;
    white-space: nowrap;
  }
  .brand-name {
    position: absolute;
    left: 438px;
    top: 306px;
    width: 160px;
    margin: 0;
    color: var(--brand-blue-deep);
    font-weight: 700;
    font-size: 16px;
    line-height: 15px;
    letter-spacing: 0.1px;
    white-space: nowrap;
  }
  .licence {
    position: absolute;
    left: 925px;
    top: 253px;
    width: 120px;
    text-align: center;
    color: var(--text-dark);
    font-size: 7.5px;
    line-height: 11px;
    margin: 0;
    white-space: nowrap;
  }
</style>
</head>
<body>
  <main class="wrap-side">
    <svg class="wrap-shapes" width="1200" height="513" viewBox="0 0 1200 513" aria-hidden="true">
      <rect class="van-body" x="30" y="60" width="1135" height="382" rx="26" fill="var(--body-white)"/>
      <polygon class="accent-grey-top" points="112,61 180,61 141,174" fill="var(--wrap-grey)"/>
      <polygon class="accent-grey-bottom" points="361,291 361,441 476,441" fill="var(--wrap-grey)"/>
      <polygon class="band-blue" points="178,60 448,60 345,373 70,373" fill="var(--brand-blue)"/>
      <rect class="brand-square" x="438" y="165" width="144" height="137" fill="var(--brand-blue)"/>
      <path class="arch-blue" d="M846,441 C846,350 890,290 965,284 C1020,280 1070,300 1080,330 L1060,352 C1040,330 1000,318 970,320 C915,325 885,375 884,441 Z" fill="var(--brand-blue)"/>
    </svg>

    <div class="services">
      <div>- ELECTRICAL -</div>
      <div>- AIR CONDITIONING -</div>
      <div>- REFRIGERATION -</div>
      <div class="services-rule"></div>
      <div class="service-area">Perth &amp; Remote WA</div>
    </div>

    <p class="phone">0412 555 318</p>

    <p class="brand-name">TALLWOOD<br>ELECTRICAL &amp;<br>REFRIGERATION</p>

    <p class="licence">Licence Nos:<br>AU531207 &amp; EC42918</p>
  </main>
</body>
</html>
```